Tallow Crest - Facebook Cover Photo & Photo Icon Design

We’re looking for a Facebook Cover Photo and Profile Icon design for Tallow Crest, a leading Residential Real Estate brand under Kestmore Property Agents, based in Capalaba and Alexandra Hills, Queensland, Australia.

This design will represent my professional real estate profile and needs to be bold, clean, and on-brand.

Deliverables:

Facebook Cover Photo (820 x 312 px, optimized for mobile + desktop)

Facebook Profile Icon (1:1 ratio, minimum 320 x 320 px)

Design Guidelines:

1. Must Include:

The Tallow Crest logo (provided after project start)

Use of the Kestmore Property Agents brand colour palette (will be supplied)

Clear connection to residential real estate

2. Optional but Preferred:

A local photo or skyline of Capalaba or Alexandra Hills in QLD (bonus points for this)

Space for a short tagline like:
“Selling Faster. Selling Smarter. Selling Kestmore.”
(Optional tagline – open to variations if it improves layout/design)

3. Style & Feel:

Professional yet personable

Clean, modern aesthetic

Subtle touches of fun or personality are welcome

Layout must work well when overlaid by Facebook UI elements (like profile photo & call-to-action buttons)

Who I Am:
I'm a well-known residential real estate agent in the Redlands area, known for high-energy campaigns, premium video marketing, and a results-driven approach. My brand is fun, fresh, and high-performing — just like the real estate campaigns I run.

Files to be Provided (after selection):

Tallow Crest logo in high-res

Brand colour palette / style reference

Optional photo references if local imagery is not sourced by designer

Final Notes:

Make sure all text is legible on mobile and desktop

Original, layered design files must be delivered (PSD or AI preferred)

Bonus points if it feels uniquely “Bayside Queensland” while maintaining a national-level professional polish

Target Market(s)

Alexandra Hills, Capalaba & Sheldon

Industry/Entity Type

Real Estate

Colors
0054AA
0677BA
7BADD7
CADEEF
E8F1F8

Requirements
Must have
• Headshot, Mobile Number 0417 962 085, Suburbs - Alexandra Hills, Capalaba & Sheldon
Nice to have
• White, Crisp & Professional. Bottom Banner with Suburb List. Specialising in Alexandra Hills, Capalaba & Sheldon

```html
<!DOCTYPE html>
<html lang="en">
<head>
<meta charset="utf-8">
<title>Tallow Crest – Facebook Cover &amp; Profile Icon</title>
<link href="https://fonts.googleapis.com/css2?family=Josefin+Sans:wght@300;400&family=Oswald:wght@300;700&family=Montserrat:wght@400;600&display=swap" rel="stylesheet">
<style>
  :root {
    --navy: #0c1b66;
    --ink: #16236e;
    --white: #ffffff;
    --stage: #eef1f3;
    --sky-top: #cfe6f2;
    --sky-low: #7badd7;
    --canopy: #4f7a4c;
    --roofs: #5d7fa8;
    --portrait-top: #c9d3dc;
    --portrait-low: #3d4a62;
  }
  * { margin: 0; padding: 0; box-sizing: border-box; }
  html, body { width: 856px; height: 1200px; overflow: hidden; }
  body { background: var(--stage); position: relative; font-family: "Montserrat", sans-serif; }

  .icon-section { position: absolute; left: 0; top: 0; width: 856px; height: 500px; background: var(--stage); }
  .cover-section { position: absolute; left: 0; top: 500px; width: 856px; height: 700px; background: var(--navy); }

  .profile-icon {
    position: absolute; left: 278px; top: 110px;
    width: 300px; height: 300px; background: var(--navy);
    display: flex; flex-direction: column; align-items: center; justify-content: center;
    color: var(--white); font-family: "Josefin Sans", sans-serif; font-weight: 300;
  }
  .profile-icon .brand-top { font-size: 26px; letter-spacing: 3px; line-height: 1; }
  .profile-icon .brand-main { font-size: 62px; letter-spacing: 6px; line-height: 1; margin-top: 4px; }

  .cover { position: absolute; left: 40px; top: 560px; width: 776px; height: 295px; display: block; }
  .tagline { font-family: "Oswald", sans-serif; fill: var(--white); }
  .tagline .bold { font-weight: 700; }
  .tagline .light { font-weight: 300; }
  .cover-logo { font-family: "Josefin Sans", sans-serif; font-weight: 300; fill: var(--ink); }
  .cover-phone { font-family: "Montserrat", sans-serif; font-weight: 400; fill: var(--ink); font-size: 19px; }
  .cover-suburbs { font-family: "Montserrat", sans-serif; font-weight: 600; fill: var(--ink); font-size: 9px; letter-spacing: 1px; }
  .cover-web { font-family: "Montserrat", sans-serif; font-weight: 600; fill: var(--ink); font-size: 7.5px; }
</style>
</head>
<body>

  <section class="icon-section">
    <div class="profile-icon" aria-label="Tallow Crest profile icon">
      <span class="brand-top">TALLOW</span>
      <span class="brand-main">CREST</span>
    </div>
  </section>

  <section class="cover-section"></section>

  <svg class="cover" viewBox="0 0 820 312" aria-label="Tallow Crest Facebook cover">
    <defs>
      <linearGradient id="aerial" x1="0" y1="0" x2="0" y2="1">
        <stop offset="0" stop-color="var(--sky-top)"/>
        <stop offset="0.12" stop-color="var(--sky-low)"/>
        <stop offset="0.22" stop-color="var(--canopy)"/>
        <stop offset="0.6" stop-color="var(--roofs)"/>
        <stop offset="1" stop-color="#6e8db5"/>
      </linearGradient>
      <linearGradient id="portrait" x1="0" y1="0" x2="0" y2="1">
        <stop offset="0" stop-color="var(--portrait-top)" stop-opacity="0.55"/>
        <stop offset="1" stop-color="var(--portrait-low)" stop-opacity="0.85"/>
      </linearGradient>
    </defs>

    <rect class="aerial-photo" x="0" y="0" width="820" height="312" fill="url(#aerial)" role="img" aria-label="Aerial photo of leafy bayside suburb homes under a blue sky"/>

    <rect class="agent-photo" x="140" y="28" width="232" height="250" rx="6" fill="url(#portrait)" role="img" aria-label="Headshot of the agent in a blazer and white shirt"/>

    <path class="white-swoosh" d="M0,272 C200,262 600,235 820,125 L820,312 L0,312 Z" fill="var(--white)"/>

    <path class="social-tab" d="M25,312 L25,256 Q25,243 38,243 L130,243 L130,312 Z" fill="var(--navy)"/>
    <circle cx="50" cy="280" r="6.5" fill="none" stroke="var(--white)" stroke-width="2"/>
    <circle cx="72" cy="280" r="6.5" fill="none" stroke="var(--white)" stroke-width="2"/>
    <circle cx="94" cy="280" r="6.5" fill="none" stroke="var(--white)" stroke-width="2"/>

    <g class="tagline">
      <text x="400" y="80" font-size="42" textLength="220" lengthAdjust="spacingAndGlyphs"><tspan class="bold">SELLING </tspan><tspan class="light">SMARTER</tspan></text>
      <text x="400" y="120" font-size="42" textLength="222" lengthAdjust="spacingAndGlyphs"><tspan class="light">SELLING </tspan><tspan class="bold">FASTER</tspan></text>
      <text x="400" y="160" font-size="42" textLength="220" lengthAdjust="spacingAndGlyphs"><tspan class="bold">SELLING </tspan><tspan class="light">KESTMORE</tspan></text>
    </g>

    <text class="cover-logo" x="722" y="232" font-size="17" text-anchor="middle" letter-spacing="2">TALLOW</text>
    <text class="cover-logo" x="722" y="265" font-size="34" text-anchor="middle" letter-spacing="3">CREST</text>
    <text class="cover-web" x="722" y="284" text-anchor="middle">www.tallowcrest-homes.com</text>

    <text class="cover-phone" x="141" y="297">0417 962 085</text>
    <text class="cover-suburbs" x="300" y="296">ALEXANDRA HILLS · CAPALABA · SHELDON</text>
  </svg>

</body>
</html>
```